Business Card for a Jewellery Brand

Business card for an upscale jewellery brand. Attached is the brand logo and icon and color board. I am looking for two card versions: one for the founder and one is generic. The card should be elegant and convey upscale and premium feel. I am open to both square and rectangle card shapes.

Industry/Entity Type

Jewelry

Contact Information for Business Card

Two cards: (1) Sunela Parvaniya (Founder) (2) General
(1) Sunela Parvaniya card should have Name: Sunela Parvaniya, Title: Founder Email id: sunela@quiremo.com.au. Phone no: +61452913307
(2) Generic card should have Email id: info@quiremo.com.au. Phone no: +61436207518

Requirements
Must have
• Workmark
• ICON
• Phone no
• Email ID
• ABN: 58219740312 (Note: ABN is Business number in Australia)
• Website: www.quiremo.com.au
• Instagram: quiremo_jewellery
• Facebook: @quiremojewellery
Nice to have
• Tagline

```html
<!DOCTYPE html>
<html lang="en">
<head>
<meta charset="utf-8">
<title>Quiremo Business Cards</title>
<link href="https://fonts.googleapis.com/css2?family=Lato:wght@300;400;700&display=swap" rel="stylesheet">
<style>
  :root {
    --rose: #e5968f;
    --rose-deep: #de837d;
    --blush: #fbe3de;
    --paper: #ffffff;
    --stage: #e9e9ea;
  }
  * { box-sizing: border-box; margin: 0; padding: 0; }
  html, body { width: 1200px; height: 880px; overflow: hidden; }
  body {
    background: var(--stage);
    font-family: "Lato", Arial, sans-serif;
    position: relative;
  }
  .card {
    position: absolute;
    width: 620px;
    height: 354px;
    border-radius: 22px;
    overflow: hidden;
    box-shadow: 0 10px 28px rgba(0,0,0,0.18);
  }
  .card-front {
    left: 120px;
    top: 60px;
    background: var(--rose);
    display: flex;
    align-items: center;
    justify-content: center;
  }
  .front-wordmark {
    color: var(--paper);
    font-weight: 400;
    font-size: 62px;
    letter-spacing: 16px;
    padding-left: 16px;
  }
  .card-back {
    left: 460px;
    top: 466px;
    background: var(--paper);
  }
  .back-wave {
    position: absolute;
    inset: 0;
    width: 100%;
    height: 100%;
  }
  .edge-dot {
    position: absolute;
    left: -14px;
    top: 122px;
    width: 28px;
    height: 28px;
    border-radius: 50%;
    background: var(--blush);
  }
  .brand-mark {
    position: absolute;
    right: 40px;
    top: 34px;
    display: flex;
    flex-direction: column;
    align-items: center;
    gap: 14px;
  }
  .brand-dot {
    width: 44px;
    height: 44px;
    border-radius: 50%;
    background: var(--rose);
  }
  .brand-name {
    color: var(--rose);
    font-weight: 400;
    font-size: 36px;
    letter-spacing: 9px;
    padding-left: 9px;
    line-height: 1.1;
  }
  .person {
    position: absolute;
    left: 46px;
    top: 92px;
    color: var(--rose);
  }
  .person-name { font-weight: 700; font-size: 23px; line-height: 1.05; }
  .person-title { font-weight: 400; font-size: 15px; }
  .contacts {
    position: absolute;
    left: 52px;
    top: 168px;
    list-style: none;
    color: var(--rose);
    font-size: 15px;
    line-height: 21px;
  }
  .contacts li { display: flex; align-items: center; gap: 8px; }
  .contact-icon {
    width: 16px; height: 16px;
    border-radius: 50%;
    background: var(--rose);
    display: inline-flex;
    align-items: center;
    justify-content: center;
    flex: none;
  }
  .abn {
    position: absolute;
    left: 52px;
    top: 262px;
    color: var(--rose);
    font-size: 16px;
    letter-spacing: 0.5px;
  }
  .website {
    position: absolute;
    right: 40px;
    bottom: 64px;
    color: var(--paper);
    font-size: 14px;
    letter-spacing: 0.5px;
  }
</style>
</head>
<body>

  <section class="card card-front">
    <div class="front-wordmark">QUIREMO</div>
  </section>

  <section class="card card-back">
    <svg class="back-wave" viewBox="0 0 620 354" preserveAspectRatio="none" aria-hidden="true">
      <path d="M0 298 C 200 304 330 272 410 225 C 470 190 540 180 620 178 L620 190 C 540 192 478 200 420 232 C 330 282 210 316 0 314 Z" fill="#fbe3de"/>
      <path d="M0 322 C 200 324 330 292 420 244 C 480 210 540 202 620 198 L620 354 L0 354 Z" fill="#e5968f"/>
    </svg>
    <div class="edge-dot"></div>

    <div class="brand-mark">
      <div class="brand-dot"></div>
      <div class="brand-name">QUIREMO</div>
    </div>

    <div class="person">
      <div class="person-name">Sunela Parvaniya</div>
      <div class="person-title">Founder</div>
    </div>

    <ul class="contacts">
      <li>
        <span class="contact-icon">
          <svg width="10" height="10" viewBox="0 0 10 10"><path d="M2 1 L4 1 L4.6 3 L3.6 3.8 C4.2 5 5 5.8 6.2 6.4 L7 5.4 L9 6 L9 8 C9 8.6 8.6 9 8 9 C4.5 9 1 5.5 1 2 C1 1.4 1.4 1 2 1 Z" fill="#fff"/></svg>
        </span>+61452913307
      </li>
      <li>
        <span class="contact-icon">
          <svg width="10" height="10" viewBox="0 0 10 10"><rect x="1" y="2.5" width="8" height="5.5" rx="0.6" fill="#fff"/><path d="M1.3 2.8 L5 5.6 L8.7 2.8" stroke="#e5968f" stroke-width="0.8" fill="none"/></svg>
        </span>sunela@quiremo.com.au
      </li>
      <li><span class="contact-icon"></span>quiremo_jewellery</li>
      <li><span class="contact-icon"></span>@quiremojewellery</li>
    </ul>

    <div class="abn">ABN: 58219740312</div>
    <div class="website">www.quiremo.com.au</div>
  </section>

</body>
</html>
```